PowerPoint Presentation 10 Slides Needed with custom graphics and possibly animated gifs

I'm creating an educational webinar for professionals. I have 10 slides that need special treatment--effective visuals that really Deliverables10 PowerPoint slides in shared PPT fileWith 10 or more images that communicate the message described in the slides notes for each slide.DeadlineSlides will be used in a PowerPoint presentation Monday, Dec 10.Due date is Friday, Dec 7.Design GuidanceSee attached deck for existing design template/theme (with colors/logo)You should match the designAnimations should be delivered as GIF files that can appear in a slideAnimation can last 4 to 10 seconds.Instead of animations, photos from Framebarrel can be recommended (I have an account and can provide the final file to use).

```html
<!DOCTYPE html>
<html lang="en">
<head>
<meta charset="utf-8">
<title>Communicare means to share</title>
<link rel="stylesheet" href="https://fonts.googleapis.com/css2?family=Fira+Sans:wght@400;600;700&family=Oswald:wght@500&display=swap">
<style>
  :root {
    --bg-light: #fbfbfc;
    --bg-dark: #e6e8ea;
    --brand-blue: #233f97;
    --brand-green: #1b7a3c;
    --text-green: #2d7a34;
    --ring-green: #3c9b4f;
    --body-gray: #6e6e6e;
    --white: #ffffff;
  }
  * { margin: 0; padding: 0; box-sizing: border-box; }
  html, body { width: 1200px; height: 674px; overflow: hidden; }
  body { font-family: "Fira Sans", Arial, sans-serif; }

  .slide {
    position: relative;
    width: 1200px;
    height: 674px;
    overflow: hidden;
    background: radial-gradient(ellipse at 90% 10%, var(--bg-light) 0%, #f1f2f3 45%, var(--bg-dark) 100%);
  }

  .accent-bar {
    position: absolute;
    left: 0; top: 195px;
    width: 33px; height: 282px;
    background: var(--brand-green);
  }

  .brand {
    position: absolute;
    top: 60px; left: 960px;
    display: flex; align-items: center; gap: 12px;
  }
  .brand-dot {
    width: 16px; height: 16px; border-radius: 50%;
    background: var(--brand-blue);
  }
  .brand-name {
    font-weight: 700; font-size: 24px;
    color: var(--brand-blue);
  }

  .intro { position: absolute; left: 66px; top: 188px; width: 270px; }
  .intro-title {
    font-size: 36px; line-height: 42px;
    color: var(--brand-blue); font-weight: 400;
  }
  .intro-title strong { font-weight: 700; display: block; }
  .intro-body {
    margin-top: 32px;
    font-size: 22px; line-height: 35px;
    color: var(--body-gray);
  }

  .lead {
    position: absolute; left: 546px; top: 218px;
    font-size: 19px; color: var(--text-green);
  }

  .elements { position: absolute; left: 0; top: 0; }
  .element-label {
    font-family: "Oswald", "Arial Narrow", sans-serif;
    font-weight: 500; fill: var(--white);
    text-anchor: middle;
  }

  .note {
    position: absolute; left: 0; width: 1482px; top: 565px;
    text-align: center;
    font-size: 19px; color: var(--text-green);
  }
</style>
</head>
<body>
<main class="slide">
  <div class="accent-bar"></div>

  <div class="brand">
    <span class="brand-dot"></span>
    <span class="brand-name">Kaiwa Learning</span>
  </div>

  <section class="intro">
    <h1 class="intro-title"><strong>Commicare</strong>means to share</h1>
    <p class="intro-body">The word Communication comes from late Middle English: from Old French from the verb communicare ‘to share’</p>
  </section>

  <p class="lead">To share, there must be at least:</p>

  <svg class="elements" width="1200" height="674" viewBox="0 0 1200 674" aria-label="Giver, the gift, the recipient">
    <g class="element">
      <circle cx="471" cy="411" r="116" fill="none" stroke="var(--ring-green)" stroke-width="1.5"/>
      <circle cx="471" cy="411" r="106" fill="var(--brand-blue)"/>
      <text class="element-label" x="471" y="428" font-size="46">GIVER</text>
    </g>
    <g class="element">
      <circle cx="739" cy="411" r="116" fill="none" stroke="var(--ring-green)" stroke-width="1.5"/>
      <circle cx="739" cy="411" r="106" fill="var(--brand-blue)"/>
      <text class="element-label" x="739" y="428" font-size="46">THE GIFT</text>
    </g>
    <g class="element">
      <circle cx="1007" cy="411" r="116" fill="none" stroke="var(--ring-green)" stroke-width="1.5"/>
      <circle cx="1007" cy="411" r="106" fill="var(--brand-blue)"/>
      <text class="element-label" x="1007" y="394" font-size="46">THE</text>
      <text class="element-label" x="1007" y="442" font-size="46">RECIPIENT</text>
    </g>
  </svg>

  <p class="note">What may not be obvious is that there should be some kind of connection.</p>
</main>
</body>
</html>
```